Glasses Promo

I am an optometrist, and we want to get our contact lens buying patients into the habit if buying glasses, too. It's not healthy to be stranded in contact lenses, with no viable glasses options. This post-card sized card would be handed out to all patients that are purchasing contact lenses from the practice, offering a complete pair of glasses, including frames, Brevik lenses, and a one year warranty, starting at $59.
Suggestion for text: buy a year supply of contact lenses and get a complete pair of glasses (new frame, brevik lenses, 1 year warranty) for $59
Updates

Project is now guaranteed / committed.  :) Let's see what you've got!

Target Market(s)

18-40 mixed male / female, quality, 'affordable luxury'

Industry/Entity Type

Promo

Requirements
Must have
• our logo (either one), brevik logo. simple, clean, premium feel.
limit one pair per patient. it should have our address and website. (ideas/info at our website: tallowmereoptic.example )
simple, clean, would like a visual reference to glasses, either outline, silhouette, abstract, whatnot. be creative! :)
Nice to have
• facebook twitter and g+ logos
Should not have
• dinosaurs. although they are awesome.

```html
<!DOCTYPE html>
<html lang="en">
<head>
<meta charset="utf-8">
<title>Glasses Promo Postcard</title>
<link rel="stylesheet" href="https://fonts.googleapis.com/css2?family=Crimson+Text:wght@400;600&family=Open+Sans:wght@400;600&display=swap">
<style>
  :root {
    --page-bg: #d9d9db;
    --card-white: #ffffff;
    --photo-light: #f4f3f4;
    --photo-mid: #e2e0e3;
    --purple: #7d2a86;
    --purple-deep: #5c1864;
    --purple-soft: rgba(125, 42, 134, 0.55);
    --text-light: #ffffff;
  }
  * { box-sizing: border-box; margin: 0; padding: 0; }
  html, body {
    width: 1200px;
    height: 750px;
    overflow: hidden;
    background: var(--page-bg);
  }
  .postcard {
    position: absolute;
    left: 150px;
    top: 75px;
    width: 900px;
    height: 600px;
    background: var(--card-white);
    box-shadow: 0 6px 24px rgba(0, 0, 0, 0.18);
    overflow: hidden;
  }
  .hero-photo {
    position: absolute;
    inset: 0 0 180px 0;
    background: radial-gradient(ellipse at 60% 40%, var(--photo-light) 0%, var(--photo-mid) 100%);
  }
  .glasses-placeholder {
    position: absolute;
    left: 40px;
    top: 215px;
    width: 820px;
    height: 205px;
    background: linear-gradient(180deg, var(--purple-soft) 0%, rgba(125, 42, 134, 0.25) 100%);
    border-radius: 30px 30px 0 0;
  }
  .headline {
    position: absolute;
    inset: 0;
    font-family: "Crimson Text", Georgia, serif;
    color: var(--purple);
  }
  .headline-buy {
    position: absolute;
    left: 330px;
    top: 0px;
    font-size: 140px;
    line-height: 1;
    font-weight: 400;
  }
  .headline-supply {
    position: absolute;
    left: 150px;
    top: 110px;
    font-size: 82px;
    line-height: 1;
  }
  .headline-lenses {
    position: absolute;
    left: 170px;
    top: 185px;
    font-size: 54px;
    line-height: 1;
    opacity: 0.55;
  }
  .headline-offer {
    position: absolute;
    font-size: 54px;
    line-height: 1;
    color: var(--purple-deep);
    font-weight: 600;
  }
  .offer-pair { left: 80px; top: 260px; }
  .offer-glasses { left: 480px; top: 340px; }
  .terms-band {
    position: absolute;
    left: 0;
    top: 420px;
    width: 100%;
    height: 38px;
    background: var(--purple);
    display: flex;
    align-items: center;
    padding-left: 24px;
  }
  .terms-text {
    font-family: "Open Sans", Arial, sans-serif;
    font-size: 15px;
    color: var(--text-light);
    letter-spacing: 0.3px;
  }
  .brand {
    position: absolute;
    right: 60px;
    bottom: 45px;
    display: flex;
    align-items: center;
    gap: 14px;
  }
  .brand-mark {
    width: 56px;
    height: 56px;
    background: var(--purple);
  }
  .brand-name {
    font-family: "Open Sans", Arial, sans-serif;
    font-weight: 600;
    font-size: 24px;
    line-height: 1.15;
    color: var(--purple);
  }
</style>
</head>
<body>
  <main class="postcard">
    <div class="hero-photo" role="img" aria-label="Soft light grey background of blurred reading text"></div>
    <div class="glasses-placeholder" role="img" aria-label="Purple eyeglasses frame resting over the headline"></div>
    <h1 class="headline">
      <span class="headline-buy">Buy</span>
      <span class="headline-supply">a year supply</span>
      <span class="headline-lenses">of contact lenses and</span>
      <span class="headline-offer offer-pair">get a pair</span>
      <span class="headline-offer offer-glasses">of glasses*</span>
    </h1>
    <div class="terms-band">
      <p class="terms-text">* For just $59. You receive a new frame with Brevik lenses and 1 year warranty</p>
    </div>
    <div class="brand">
      <span class="brand-mark"></span>
      <span class="brand-name">Tallowmere Optic<br>Associates</span>
    </div>
  </main>
</body>
</html>
```